Millcrest PTA Website Design

We are working with Millcrest Elementary School PTA. They are a Parent Teacher Association that needs a new website design.

A Parent Teacher Association (PTA) is a volunteer organization that brings parents, teachers, and school staff together to support students and enhance their educational experience. PTAs organize fundraisers, sponsor school events, advocate for education policies, and foster stronger connections between families and schools.

Some sites to use for inspiration:

https://parentboardhub.com/demo/
https://nonprofits.kindlyfundr.com/blogs/more-great-pta-websites-you-should-copy
https://www.rvmxpta.com

Thank you for taking the time to consider designing a website for us. We are web developers based in Stockton and Los Angeles, CA, USA. Most of our projects go through the same process. Understanding this process may help you win a project with us. We custom-code all of our websites in-house. We don’t have any requirements as to what tools you use for your design, but we prefer Figma files. For any design that we label as four-stars, we send it to the client for review. The client picks the final design they want us to use. Once we complete this process, we will continue to show additional clients all the four-star sites and purchase them later. Your designs will have multiple chances to sell. For better chances of success, we ask that you follow these guidelines.

IMAGES:
If you use any images or icons in the design, we ask that you have a link to the asset so we can purchase the image/icon. Most of the designs we submit do not have the customer’s images on them unless they have some great images. Be creative; show us the feeling you are trying to portray with your image choices. Use any royalty-free site you choose. We subscribe to Adobe and mainly use their images, but we can purchase images outside of Adobe.

PLEASE NOTE: we will not submit designs to clients with watermarks on the images.

FONTS:
We ask that you identify the fonts used in the design. This can be done in a message if you want. We typically use Google Fonts and Adobe Fonts.

CONTENT:
We're always open to different content and ideas. We often submit designs with stock images so the client can see our vision. We typically take pictures after the website launch to use their images with our vision. Lorem Ipsum is fine for paragraphs, but we ask that you write the headers in correct English. We want to be able to show the vision and identify the sections of the website.

INSPIRATION:
We typically add a couple of links in the brief of websites we like to help you get started in your design.

REVISIONS:
We do not often ask for revisions of the designs unless we see something in the design that may not appeal to the client. If there are slight changes that we want to make, we do that in the development process.

FEEDBACK:
We rarely give feedback on designs during the design process. We are working on many website projects and do not have the time to provide feedback. We usually respond if your request is well thought out and asks specific questions, but a note asking “feedback, please” usually goes unanswered.

```html
<!DOCTYPE html>
<html lang="en">
<head>
<meta charset="utf-8">
<title>Millcrest PTA</title>
<link href="https://fonts.googleapis.com/css2?family=Poppins:wght@400;500;600;700&display=swap" rel="stylesheet">
<style>
:root{
  --navy:#1d2e8c;
  --navy-deep:#162470;
  --ink:#1c2b78;
  --text:#4a4f63;
  --muted:#8a8fa0;
  --light:#f1f2f5;
  --white:#ffffff;
  --line:#e3e5ec;
}
*{box-sizing:border-box;margin:0;padding:0}
html,body{width:1200px;height:4702px;overflow:hidden}
body{font-family:"Poppins",sans-serif;color:var(--text);background:var(--white);position:relative}
.abs{position:absolute}
.photo{position:absolute}
.topbar{position:absolute;left:0;top:0;width:1200px;height:37px;background:var(--navy);color:var(--white);font-size:12px}
.topbar .item{position:absolute;top:11px;display:flex;align-items:center;gap:6px}
.topbar svg{width:11px;height:11px;fill:var(--white)}
.topbar .social{position:absolute;left:1078px;top:9px;width:19px;height:19px;background:var(--white)}
.header{position:absolute;left:0;top:37px;width:1200px;height:73px;background:var(--white)}
.brand{position:absolute;left:100px;top:21px;font-weight:700;font-size:12px;line-height:14px;color:var(--navy);width:90px}
.nav{position:absolute;left:223px;top:29px;display:flex;gap:28px;font-size:10px;font-weight:600;color:var(--navy)}
.btn{display:inline-flex;align-items:center;justify-content:center;font-size:10px;font-weight:600;letter-spacing:.3px}
.btn-outline{position:absolute;left:928px;top:21px;width:60px;height:31px;border:1.5px solid var(--navy);color:var(--navy)}
.btn-solid{position:absolute;left:997px;top:21px;width:100px;height:31px;background:var(--navy);color:var(--white)}
.hero{position:absolute;left:0;top:110px;width:1200px;height:620px;background:linear-gradient(100deg,#2c3e2a 0%,#4d6a35 30%,#8a5a3e 58%,#a7452f 75%,#c9c2b6 100%)}
.hero .shade{position:absolute;inset:0;background:linear-gradient(90deg,rgba(10,20,40,.55) 0%,rgba(10,20,40,.2) 55%,rgba(0,0,0,0) 100%)}
.hero .kicker{position:absolute;left:100px;top:218px;color:var(--white);font-size:13px;font-weight:500;letter-spacing:3px}
.hero h1{position:absolute;left:100px;top:246px;color:var(--white);font-size:44px;line-height:49px;font-weight:600}
.hero p{position:absolute;left:100px;top:350px;color:var(--white);font-size:12px}
.hero .cta{position:absolute;left:100px;top:391px;width:101px;height:31px;background:var(--white);color:var(--navy)}
h2.section-title{position:absolute;left:0;width:1200px;text-align:center;font-size:34px;font-weight:600;color:var(--navy);letter-spacing:.5px}
.about-text{position:absolute;left:450px;top:925px;width:315px;text-align:center}
.about-text h2{font-size:33px;font-weight:600;color:var(--navy);margin-bottom:10px}
.about-text p{font-size:11.5px;line-height:19px;color:var(--text);margin-bottom:16px}
.about-text .btn{width:102px;height:31px;background:var(--navy);color:var(--white)}
.service{position:absolute;top:1433px;width:238px;height:278px;background:var(--white);box-shadow:0 2px 10px rgba(20,30,80,.12);text-align:center;padding-top:44px}
.service svg{width:74px;height:74px;stroke:var(--ink);fill:none;stroke-width:2.4;stroke-linecap:round;stroke-linejoin:round}
.service h3{font-size:18px;font-weight:500;color:var(--navy);margin-top:26px;letter-spacing:.5px}
.service p{font-size:11.5px;line-height:19px;color:var(--text);margin:8px 14px 0}
.join{position:absolute;left:0;top:1795px;width:1200px;height:498px;background:linear-gradient(90deg,var(--navy-deep) 0%,var(--navy) 55%,#2a3c9a 100%)}
.join h2{position:absolute;left:630px;top:155px;color:var(--white);font-size:32px;font-weight:600}
.join p{position:absolute;left:632px;top:205px;width:380px;color:var(--white);font-size:11.5px;line-height:19px}
.mark-box{position:absolute;display:flex;flex-direction:column;justify-content:flex-end;font-weight:700;line-height:1}
.prog{position:absolute;top:2465px;width:276px;height:424px;background:var(--white);box-shadow:0 3px 12px rgba(20,30,80,.14)}
.prog .img{position:absolute;left:8px;top:9px;width:260px;height:207px}
.prog h3{position:absolute;left:22px;top:236px;font-size:18px;font-weight:500;color:var(--navy);letter-spacing:.3px}
.prog p{position:absolute;left:22px;top:270px;width:238px;font-size:11.5px;line-height:19px;color:var(--text)}
.dots{position:absolute;left:567px;top:2917px;display:flex;gap:8px;align-items:center}
.dots span{width:10px;height:10px;background:#c6c9d3}
.dots span.on{background:var(--navy);transform:rotate(45deg)}
.online{position:absolute;left:0;top:2962px;width:1200px;text-align:center;font-size:11px;font-weight:600;color:var(--navy)}
.after-sub{position:absolute;left:0;top:3117px;width:1200px;text-align:center;font-size:12px;color:var(--text)}
.step{position:absolute;display:flex;align-items:center;gap:14px;font-size:18px;font-weight:500;color:var(--navy);letter-spacing:.3px}
.step svg{width:36px;height:36px;stroke:var(--ink);fill:none;stroke-width:1.8;stroke-linecap:round;stroke-linejoin:round}
.divider{position:absolute;height:1px;background:var(--line)}
.divider::before,.divider::after{content:"";position:absolute;top:-4px;width:8px;height:8px;background:var(--navy);transform:rotate(45deg)}
.divider::before{left:-4px}
.divider::after{right:-4px}
.events{position:absolute;left:0;top:3594px;width:1200px;height:661px;background:linear-gradient(90deg,var(--navy-deep) 0%,var(--navy) 60%,#23359a 100%)}
.events h2{position:absolute;left:0;top:95px;width:1200px;text-align:center;font-size:33px;font-weight:600;color:var(--white)}
.feature-text{position:absolute;left:194px;top:4000px;width:330px;color:var(--white)}
.feature-text h3,.post h3{font-size:18px;font-weight:500;letter-spacing:.5px;line-height:22px}
.feature-text p,.post p{font-size:11.5px;line-height:19px;margin-top:10px}
.more{display:inline-block;margin-top:8px;font-size:10px;font-weight:600;text-decoration:underline;color:var(--white)}
.post{position:absolute;left:798px;width:240px;color:var(--white)}
.strip{position:absolute;left:0;top:4255px;width:1200px;height:146px;background:var(--light)}
.strip p{position:absolute;left:100px;top:65px;font-size:18px;font-weight:500;color:var(--navy);line-height:22px}
.strip .btn{position:absolute;left:951px;top:56px;width:101px;height:33px;background:var(--navy);color:var(--white)}
.foot-col{position:absolute;top:4477px}
.foot-col h4{font-size:12px;font-weight:600;color:var(--ink);margin-bottom:12px}
.foot-col li{list-style:none;font-size:10px;line-height:18.5px;color:var(--muted)}
.foot-col .row{display:flex;gap:8px;font-size:10px;line-height:14px;color:var(--muted);margin-bottom:8px}
.foot-col .row svg{width:10px;height:10px;fill:var(--navy);flex:none;margin-top:2px}
.field{width:175px;border-bottom:1px solid var(--line);font-size:8px;color:var(--muted);padding:6px 0;letter-spacing:1px;margin:10px 0 12px}
.foot-col .btn{width:100px;height:31px;background:var(--navy);color:var(--white)}
.copyright{position:absolute;left:0;top:4669px;width:1200px;text-align:center;font-size:10px;color:var(--text)}
.chat{position:absolute;left:1137px;top:4640px;width:30px;height:30px;border-radius:50%;background:var(--navy)}
</style>
</head>
<body>

<div class="topbar">
  <div class="item" style="left:100px"><svg viewBox="0 0 10 10"><path d="M0 2h10v6H0z M0 2l5 3 5-3" /></svg>ptamillcrestlions@millcrestpta.org</div>
  <div class="item" style="left:320px"><svg viewBox="0 0 10 10"><path d="M2 0l2 2-1 2 3 3 2-1 2 2-2 2C4 10 0 6 0 2z"/></svg>(209)555-0148</div>
  <div class="item" style="left:451px"><svg viewBox="0 0 10 10"><path d="M5 0a3.5 3.5 0 0 1 3.5 3.5C8.5 6 5 10 5 10S1.5 6 1.5 3.5A3.5 3.5 0 0 1 5 0z"/></svg>1480 Harlow Court Riverbend, CA 95300</div>
  <div class="social" aria-label="Social page"></div>
</div>

<header class="header">
  <div class="brand">MILLCREST PTA</div>
  <nav class="nav">
    <span>PTA AND YOU!</span><span>MILLCREST PTA STORE</span><span>PTA-FUNDED PROGAMS</span><span>BLUE AND WHITE</span><span>MILLCREST ELEMENTARY WEBSITE</span>
  </nav>
  <span class="btn btn-outline">LOGIN</span>
  <span class="btn btn-solid">CONTACT US</span>
</header>

<section class="hero">
  <div class="photo" style="inset:0" role="img" aria-label="Historic red brick school building behind a large green tree"></div>
  <div class="shade"></div>
  <div class="kicker">WELCOME TO LIONS</div>
  <h1>TOGETHER WE GROW,<br>LEARN &amp; INSPIRE</h1>
  <p>Join parents, teachers, and students in building a stronger school community.</p>
  <span class="btn cta">JOIN THE PTA</span>
</section>

<section class="about">
  <div class="photo" style="left:100px;top:853px;width:324px;height:429px;background:linear-gradient(160deg,#c9b79c,#8a7560 55%,#2f3550)" role="img" aria-label="Two schoolgirls in uniforms chatting and laughing"></div>
  <div class="about-text">
    <h2>ABOUT US LIONS</h2>
    <p>Welcome back to Millcrest Elementary School and the 2019-2020 school year! We are looking forward to a great year in which we continue a tradition of excellence. Our PTA theme this year is Millcrest Lions: Tell the Tale</p>
    <p>The Millcrest PTA is a very active organization. We raise funds, provide key programs and work with our teachers on a cooperative basis. Most importantly, we advocate for your Millcrest student to ensure all their needs are met.</p>
    <span class="btn">READ MORE</span>
  </div>
  <div class="photo" style="left:789px;top:849px;width:221px;height:265px;background:linear-gradient(170deg,#7fa7c9,#d9c15a 60%,#b9a988)" role="img" aria-label="Parent greeting a young student with a backpack"></div>
  <div class="photo" style="left:886px;top:1090px;width:241px;height:197px;background:linear-gradient(160deg,#6f9d52,#b58a6a 55%,#3a4b6c)" role="img" aria-label="Group of smiling students outdoors"></div>
</section>

<h2 class="section-title" style="top:1365px">OUR SERVICES</h2>
<div class="service" style="left:100px">
  <svg viewBox="0 0 74 74"><rect x="12" y="20" width="50" height="42"/><path d="M12 32h50M24 12v14M50 12v14M37 38l4 8 8 1-6 5 2 8-8-4-8 4 2-8-6-5 8-1z"/></svg>
  <h3>EVENTS</h3><p>Lorem Ipsum is simply dummy text of the printing and typesetting industry. Lorem Ipsum has been the</p>
</div>
<div class="service" style="left:354px">
  <svg viewBox="0 0 74 74"><circle cx="26" cy="24" r="9"/><circle cx="50" cy="24" r="9"/><path d="M10 60c0-12 7-20 16-20s16 8 16 20M34 60c0-12 7-20 16-20s16 8 16 20"/></svg>
  <h3>JOIN THE PTA</h3><p>Lorem Ipsum is simply dummy text of the printing and typesetting industry. Lorem Ipsum has been the</p>
</div>
<div class="service" style="left:608px">
  <svg viewBox="0 0 74 74"><path d="M14 26h46l-4 36H18z M27 26v-6a10 10 0 0 1 20 0v6"/></svg>
  <h3>SPIRIT STORE</h3><p>Lorem Ipsum is simply dummy text of the printing and typesetting industry. Lorem Ipsum has been the</p>
</div>
<div class="service" style="left:860px">
  <svg viewBox="0 0 74 74"><path d="M10 30l27-18 27 18v32H10z M10 30l27 20 27-20 M22 22h30v18"/></svg>
  <h3>NEWSLETTERS</h3><p>Lorem Ipsum is simply dummy text of the printing and typesetting industry. Lorem Ipsum has been the</p>
</div>

<section class="join">
  <div class="photo" style="left:161px;top:62px;width:325px;height:374px;background:linear-gradient(150deg,#b68b3c,#6b5a48 50%,#2c2f45)" role="img" aria-label="Smiling boy with a backpack greeting an adult"></div>
  <div class="mark-box" style="left:420px;top:150px;width:137px;height:192px;background:var(--navy);border:3px solid var(--white);color:var(--white);font-size:22px;padding:0 14px 18px">MILLCREST<br>PTA</div>
  <h2>HOW DO I JOIN PTA?</h2>
  <p>We need members to make all this happen ... working parents, at-home parents, single parents, grandparents, aunts, uncles, guardians, whatever the case may be...we value you and your participation and input. Signing up is simple, just print the PTA membership application, fill it out, and return it to your child's teacher or the school office by Friday, August 30.</p>
</section>

<h2 class="section-title" style="top:2396px">PTA-FUNDED PROGRAMS</h2>
<div class="prog" style="left:170px">
  <div class="img" style="background:linear-gradient(120deg,#ffffff 30%,#e53b2f 48%,#f5a623 56%,#f7e03c 64%,#3bb54a 72%,#2f6fd6 82%,#7b3fb5 92%)" role="img" aria-label="Paintbrush painting a rainbow stripe"></div>
  <h3>ART PROGRAM</h3>
  <p>Through fundraising and generous donations, our PTA fully funds our entire art program - that means the teacher's full salary and all the supplies! That's nearly $18,000 a year to make sure your student gets art lessons every single month!</p>
</div>
<div class="prog" style="left:462px">
  <div class="img" style="background:linear-gradient(135deg,#c98b4a,#e0a85c 40%,#3d8fd1 60%,#e24a5a 80%,#6b6f78)" role="img" aria-label="Colorful school supplies on a wooden desk"></div>
  <h3>TEACHER SUPPLIES</h3>
  <p>With education budgets being tightened, we like to support our teachers in the big things as well as the little. That's why we like to provide each teacher at Millcrest with extra school supply funds so that they spend less out of pocket and can get more for your child.</p>
</div>
<div class="prog" style="left:754px">
  <div class="img" style="background:radial-gradient(ellipse at 50% 55%,#f6c623 0%,#f6c623 35%,#ffffff 62%)" role="img" aria-label="Cartoon yellow field trip bus"></div>
  <h3>FIELD TRIPS</h3>
  <p>Out-of-class experiences are often the ones that really drive home the lessons learned while sitting at a desk. Each year, our students get the opportunity to go on field trips. Though we ask for donations, PTA typically willingly picks up...</p>
</div>
<div class="dots"><span></span><span class="on"></span><span></span><span></span></div>
<p class="online">OR JOIN ONLINE VIA MEMBLY AT: HTTPS://JOINMEMBLY.COM/CA/RIVERBEND/MILLCREST-ELEMENTARY-PTA</p>

<h2 class="section-title" style="top:3068px">AFTER I JOIN PTA, THEN WHAT?</h2>
<p class="after-sub">There are many ways to get involved based on your own schedule:</p>

<div class="step" style="right:763px;top:3225px">VOLUNTEERING<svg viewBox="0 0 36 36"><path d="M6 20l8 8 16-16M10 10h10"/></svg></div>
<div class="step" style="right:763px;top:3316px">EVERYDAY FUNDRAISING<svg viewBox="0 0 36 36"><circle cx="18" cy="14" r="8"/><path d="M8 30h20M18 10v8"/></svg></div>
<div class="step" style="right:763px;top:3409px">JOG-A-THON<svg viewBox="0 0 36 36"><path d="M4 26l6-12 8 4 8 2 6 4v4H4z"/></svg></div>
<div class="divider" style="left:150px;top:3285px;width:334px"></div>
<div class="divider" style="left:150px;top:3378px;width:334px"></div>

<div class="mark-box" style="left:489px;top:3196px;width:219px;height:292px;color:var(--navy);font-size:36px;align-items:center;text-align:center;justify-content:center">
  <span style="display:block;width:64px;height:64px;background:var(--navy);margin-bottom:18px"></span>MILLCREST<br>PTA
</div>

<div class="step" style="left:752px;top:3225px"><svg viewBox="0 0 36 36"><rect x="6" y="8" width="24" height="20"/><path d="M12 16h12M12 22h8"/></svg>FIELD TRIP DONATION</div>
<div class="step" style="left:752px;top:3316px"><svg viewBox="0 0 36 36"><path d="M12 6l-8 6 4 6 4-2v14h12V16l4 2 4-6-8-6c-2 3-10 3-12 0z"/></svg>SPIRIT WEAR</div>
<div class="step" style="left:752px;top:3409px"><svg viewBox="0 0 36 36"><rect x="5" y="8" width="26" height="22"/><path d="M5 15h26M12 4v8M24 4v8"/></svg>FAMILY EVENTS</div>
<div class="divider" style="left:722px;top:3285px;width:304px"></div>
<div class="divider" style="left:722px;top:3378px;width:304px"></div>

<section class="events">
  <h2>OUR EVENTS</h2>
</section>
<div class="photo" style="left:172px;top:3752px;width:368px;height:408px;background:linear-gradient(170deg,#7a5a3e,#5a4636 50%,#2b2320)" role="img" aria-label="Family reading together on a couch"></div>
<div class="feature-text">
  <h3>ACME POLL – MEMBER SURVEY</h3>
  <p>We have so many great ideas you guys give us, and we've discussed them and want more feedback from you! Please fill out the poll below on your ...</p>
  <span class="more">READ MORE</span>
</div>
<div class="photo" style="left:555px;top:3752px;width:217px;height:198px;background:linear-gradient(160deg,#d9b48a,#3e7fc4 55%,#e0a03a)" role="img" aria-label="Children drawing together at a table"></div>
<div class="photo" style="left:555px;top:3961px;width:217px;height:199px;background:linear-gradient(160deg,#c9a483,#8f6b55 55%,#3e3a4a)" role="img" aria-label="Parent and child sharing a book"></div>
<div class="post" style="top:3775px">
  <h3>ACME WEEKLY<br>JANUARY 14</h3>
  <p>Welcome to our newsletter for the week! Check out all that is going on below. Join the ACME School PTO to receive the newsletter in your ...</p>
  <span class="more">READ MORE</span>
</div>
<div class="post" style="top:3980px">
  <h3>ACME WEEKLY<br>JANUARY 28</h3>
  <p>Welcome to our newsletter for the week! Check out all that is going on below. Join the ACME School PTO to receive the newsletter in your ...</p>
  <span class="more">READ MORE</span>
</div>

<section class="strip">
  <p>CLICK THE "JOIN PTA" BUTTON TO SUPPORT YOUR MES COMMUNITY<br>BY PURCHASING AN ANNUAL MEMBERSHIP TODAY!</p>
  <span class="btn">JOIN PTA</span>
</section>

<footer>
  <div class="abs" style="left:205px;top:4520px;font-size:20px;font-weight:700;line-height:24px;color:var(--navy)">MILLCREST<br>PTA</div>
  <div class="abs" style="left:310px;top:4584px;width:16px;height:16px;background:var(--navy)" aria-label="Social page"></div>
  <div class="foot-col" style="left:402px">
    <h4>QUICK LINKS</h4>
    <ul><li>PTA and YOU!</li><li>Millcrest PTA Store</li><li>PTA-Funded Programs</li><li>Blue and White</li><li>Millcrest Elementary</li><li>Website</li></ul>
  </div>
  <div class="foot-col" style="left:579px">
    <h4>CONTACT US</h4>
    <div class="row"><svg viewBox="0 0 10 10"><path d="M2 0l2 2-1 2 3 3 2-1 2 2-2 2C4 10 0 6 0 2z"/></svg>(209)555-0148</div>
    <div class="row"><svg viewBox="0 0 10 10"><path d="M0 2h10v6H0z"/></svg>ptamillcrestlions@millcrestpta.org</div>
    <div class="row"><svg viewBox="0 0 10 10"><path d="M5 0a3.5 3.5 0 0 1 3.5 3.5C8.5 6 5 10 5 10S1.5 6 1.5 3.5A3.5 3.5 0 0 1 5 0z"/></svg><span>1480 Harlow Court Riverbend,<br>CA 95300</span></div>
  </div>
  <div class="foot-col" style="left:818px">
    <h4>SUBSCRIBE FOR UPDATES</h4>
    <p style="font-size:9.5px;line-height:13px;width:180px;color:var(--text)">Subscribe and be the first to receive all the latest insights.</p>
    <div class="field">EMAIL</div>
    <span class="btn">SUBSCRIBE</span>
  </div>
  <div class="abs" style="left:150px;top:4638px;width:900px;height:1px;background:var(--line)"></div>
  <p class="copyright">Copyright © 2025 Millcrest PTA — Meadowline PageCraft theme by HostNimbus</p>
  <div class="chat" aria-label="Chat"></div>
</footer>

</body>
</html>
```